Dunmore Roofing

Want a professional looking business card

Industry/Entity Type

Business

Contact Information for Business Card

Paul Dunmore ( Owner) paul@dunmoreroofing-example.com, www.dunmoreroofing-example.com, Adress: 4172 Township road 43 Plantagenet,ON K9X4T2

```html
<!DOCTYPE html>
<html lang="en">
<head>
<meta charset="utf-8">
<title>Dunmore Roofing – Business Card</title>
<link rel="stylesheet" href="https://fonts.googleapis.com/css2?family=Roboto:wght@400;500&family=Roboto+Condensed:wght@700&display=swap">
<style>
  :root {
    --backdrop: #2a2a2b;
    --card-grey: #77787a;
    --swoosh-grey: #8a8b8d;
    --brand-blue: #1a4589;
    --paper: #f3f3f3;
    --ink-grey: #77787a;
    --white: #ffffff;
  }
  * { margin: 0; padding: 0; box-sizing: border-box; }
  html, body { width: 1200px; height: 960px; overflow: hidden; }
  body { background: var(--backdrop); position: relative; font-family: "Roboto", Arial, sans-serif; }

  .card { position: absolute; border-radius: 14px; overflow: hidden; }

  /* Back of card */
  .card-back { left: 320px; top: 105px; width: 605px; height: 350px; background: var(--card-grey); }
  .back-mark-area {
    position: absolute; left: 0; top: 40px; width: 466px; height: 272px;
    background: linear-gradient(135deg, var(--brand-blue) 0%, #2f558f 55%, #5f6f87 100%);
    border-radius: 0 60px 0 0;
  }
  .back-brand { position: absolute; right: 0; top: 0; width: 120px; height: 350px; }
  .back-brand .name,
  .back-brand .web {
    position: absolute; top: 175px; white-space: nowrap;
    transform-origin: center center; text-align: center;
  }
  .back-brand .name {
    left: 40px; width: 276px; margin-left: -138px; margin-top: -18px;
    transform: rotate(-90deg);
    font-family: "Roboto Condensed", Arial, sans-serif; font-weight: 700;
    font-size: 30px; letter-spacing: 2px; color: var(--brand-blue); line-height: 36px;
  }
  .back-brand .web {
    left: 75px; width: 290px; margin-left: -145px; margin-top: -9px;
    transform: rotate(-90deg);
    font-size: 13.5px; letter-spacing: 2.2px; color: var(--white); line-height: 18px;
  }

  /* Front of card */
  .card-front { left: 320px; top: 493px; width: 598px; height: 342px; background: var(--paper); }
  .card-front svg.sweep { position: absolute; inset: 0; }

  .front-brand {
    position: absolute; left: 38px; top: 110px; display: flex; align-items: center; gap: 10px;
  }
  .front-brand .mark { width: 16px; height: 16px; background: var(--brand-blue); }
  .front-brand .name {
    font-family: "Roboto Condensed", Arial, sans-serif; font-weight: 700;
    font-size: 30px; letter-spacing: 1px; color: var(--brand-blue); line-height: 34px;
  }

  .holder { position: absolute; left: 39px; top: 207px; }
  .holder .person {
    font-family: "Roboto Condensed", Arial, sans-serif; font-weight: 700;
    font-size: 23px; color: var(--brand-blue); line-height: 26px;
  }
  .holder .role { font-size: 15px; color: var(--ink-grey); letter-spacing: 0.5px; margin-top: 2px; }

  .contact {
    position: absolute; right: 32px; top: 205px; text-align: right;
    color: var(--white); font-size: 14.5px; line-height: 19px;
  }
  .contact .address { margin-bottom: 9px; padding-right: 14px; }
  .contact li { list-style: none; display: flex; justify-content: flex-end; align-items: center; gap: 5px; }
  .contact svg { width: 13px; height: 13px; fill: var(--white); }
</style>
</head>
<body>

  <section class="card card-back" aria-label="Business card back">
    <div class="back-mark-area" role="img" aria-label="Large brand mark decoration area"></div>
    <div class="back-brand">
      <div class="name">DUNMORE ROOFING</div>
      <div class="web">www.dunmoreroofing-example.com</div>
    </div>
  </section>

  <section class="card card-front" aria-label="Business card front">
    <svg class="sweep" width="598" height="342" viewBox="0 0 598 342" aria-hidden="true">
      <path d="M300 214 C410 150 470 80 440 0 L555 0 C480 130 380 190 300 214 Z" fill="var(--swoosh-grey)"/>
      <path d="M58 342 C250 255 470 175 560 0 L598 0 L598 342 Z" fill="var(--brand-blue)" stroke="var(--white)" stroke-width="3"/>
    </svg>

    <div class="front-brand">
      <span class="mark"></span>
      <span class="name">DUNMORE ROOFING</span>
    </div>

    <div class="holder">
      <div class="person">PAUL DUNMORE</div>
      <div class="role">OWNER</div>
    </div>

    <div class="contact">
      <div class="address">4172 Township road 43<br>Plantagenet, ON K9X4T2</div>
      <ul>
        <li>613 555 0148
          <svg viewBox="0 0 24 24"><path d="M6.6 10.8a15 15 0 0 0 6.6 6.6l2.2-2.2c.3-.3.7-.4 1-.2 1.1.4 2.3.6 3.6.6.6 0 1 .4 1 1V20c0 .6-.4 1-1 1A17 17 0 0 1 3 4c0-.6.4-1 1-1h3.5c.6 0 1 .4 1 1 0 1.3.2 2.5.6 3.6.1.3 0 .7-.2 1z"/></svg>
        </li>
        <li>paul@dunmoreroofing-example.com
          <svg viewBox="0 0 24 24"><path d="M2 5h20v14H2z M3 6l9 7 9-7" fill="none" stroke="#fff" stroke-width="2"/></svg>
        </li>
        <li>www.dunmoreroofing-example.com
          <svg viewBox="0 0 24 24"><circle cx="12" cy="12" r="10"/><path d="M2 12h20M12 2c3 3 3 17 0 20M12 2c-3 3-3 17 0 20" fill="none" stroke="#1a4589" stroke-width="1.6"/></svg>
        </li>
      </ul>
    </div>
  </section>

</body>
</html>
```